Toms welding and seed cleaning Business cards

Jakes welding and seed cleaningWe clean wheat seed on farm with portable cleaners so the farmers have pure wheat seed to plant back for the next crop. We are certified to clean foundation, registered, and certified seed wheat. Our cleaners being portable make it easier for the farmers because we do it right on there farm so they don't have to haul it all to townWhen there is no wheat to clean we weld in the winter. We improve, add onto, and build new corrals. We also build sheds, cattle shelters, and wind breaks. Other welding is welcomed

Reason: I need to extend the deadline because I've been busy and not had my game together. I need more time figure out what I want yet

Industry/Entity Type

Agriculture

Contact Information for Business Card

Just "toms welding and seed cleaning" on front and other info on the back
On the back side I would like to have my address.
Morris Tulane
48213 W COUNTY RD 318
ALDER CREEK OK 73790
Phone #5804419362

Font styles to use
Sans Serif

Requirements
Must have
• list we are certified to clean foundation, registered, and certified wheat
• State that they are portable cleaners
• For the welding part list, add on to, improve on, and repair existing corrals and new corrals and other welding welcomed
Nice to have
• A wheat field with some metal corrals on the side with a nice classic looking barn for a background. Maybe some cattle in the corrals
• A nice looking farm yard would be good too

```html
<!DOCTYPE html>
<html lang="en">
<head>
<meta charset="utf-8">
<title>Business card – back</title>
<link href="https://fonts.googleapis.com/css2?family=Bebas+Neue&family=Open+Sans:ital,wght@1,400&display=swap" rel="stylesheet">
<style>
  :root {
    --accent: #f7a21b;
    --ink: #ffffff;
    --field-dark: #3b2d17;
    --field-mid: #6b4d22;
    --field-gold: #a2762f;
    --sky: #5e5a55;
  }
  * { margin: 0; padding: 0; box-sizing: border-box; }
  html, body { width: 1200px; height: 741px; overflow: hidden; background: #222; }
  .card {
    position: relative;
    width: 1200px;
    height: 741px;
    overflow: hidden;
    font-family: "Bebas Neue", "Arial Narrow", sans-serif;
    color: var(--ink);
  }
  .card__photo {
    position: absolute; inset: 0;
    background:
      radial-gradient(ellipse 45% 22% at 25% 28%, rgba(214,150,60,0.55), transparent 70%),
      linear-gradient(180deg, var(--sky) 0%, #615444 14%, #8a6a38 26%, var(--field-gold) 34%, var(--field-mid) 56%, var(--field-dark) 100%);
  }
  .card__shade {
    position: absolute; inset: 0;
    background: linear-gradient(90deg, rgba(0,0,0,0.05) 0%, rgba(0,0,0,0.22) 60%, rgba(0,0,0,0.28) 100%);
  }
  .service {
    position: absolute;
    left: 614px;
    border-left: 11px solid var(--accent);
    padding-left: 24px;
  }
  .service--seed { top: 86px; height: 166px; }
  .service--welding { top: 300px; height: 357px; }
  .service__title {
    font-size: 62px;
    line-height: 50px;
    font-weight: 400;
    color: var(--accent);
    letter-spacing: 0.5px;
    margin-top: -4px;
  }
  .service--welding .service__title { line-height: 54px; margin-top: -7px; }
  .service__text {
    font-size: 41px;
    line-height: 35px;
    letter-spacing: 0.3px;
  }
  .service--seed .service__text { margin-top: 2px; }
  .service--welding .service__text { margin-top: 12px; font-size: 42px; line-height: 38px; }
  .service__list { list-style: none; margin-top: 6px; }
  .service__list li { font-size: 42px; line-height: 51px; letter-spacing: 0.3px; }
  .service__note {
    font-family: "Open Sans", Arial, sans-serif;
    font-style: italic;
    font-size: 25px;
    line-height: 28px;
    margin-top: -1px;
  }
  .contact {
    position: absolute;
    left: 71px;
    top: 447px;
  }
  .contact__name {
    font-size: 55px;
    line-height: 52px;
    color: var(--accent);
    font-weight: 400;
    margin-left: 43px;
    letter-spacing: 0.5px;
  }
  .contact__row {
    display: flex;
    align-items: flex-start;
    margin-top: 15px;
  }
  .contact__row + .contact__row { margin-top: 23px; }
  .contact__icon { width: 31px; height: 31px; flex: none; margin-right: 12px; margin-top: 3px; }
  .contact__text { font-size: 38px; line-height: 36px; letter-spacing: 0.3px; }
</style>
</head>
<body>
<main class="card">
  <div class="card__photo" role="img" aria-label="Wheat field with ripe wheat heads at sunset"></div>
  <div class="card__shade"></div>

  <section class="service service--seed">
    <h2 class="service__title">Registered and<br>certified wheat seed</h2>
    <p class="service__text">We have portable cleaning so we<br>can clean your seed on your farm</p>
  </section>

  <section class="service service--welding">
    <h2 class="service__title">Welding sevices</h2>
    <p class="service__text">We build new corrals and<br>add onto, improve, and<br>repair existing corrals</p>
    <ul class="service__list">
      <li>Sheds</li>
      <li>Cattle shelters</li>
      <li>Wind breaks</li>
    </ul>
    <p class="service__note">Other welding is welcomed</p>
  </section>

  <section class="contact">
    <h1 class="contact__name">Morris Tulane</h1>
    <div class="contact__row">
      <svg class="contact__icon" viewBox="0 0 32 32" aria-hidden="true">
        <circle cx="16" cy="16" r="16" fill="var(--accent)"/>
        <path d="M16 7 L25 15 H22 V24 H18 V19 H14 V24 H10 V15 H7 Z" fill="#fff"/>
      </svg>
      <p class="contact__text">48213 W County Rd 318<br>Alder Creek OK 73790</p>
    </div>
    <div class="contact__row">
      <svg class="contact__icon" viewBox="0 0 32 32" aria-hidden="true">
        <circle cx="16" cy="16" r="16" fill="var(--accent)"/>
        <path d="M11.5 8 L14 8 L15.5 12.5 L13.5 14 C14.5 16.5 15.8 17.8 18 18.8 L19.5 16.8 L24 18.3 L24 20.8 C24 22.5 22.5 23.8 20.8 23.5 C14.5 22.5 9.5 17.5 8.5 11.2 C8.2 9.5 9.6 8 11.5 8 Z" fill="#fff"/>
      </svg>
      <p class="contact__text">Phone #5804419362</p>
    </div>
  </section>
</main>
</body>
</html>
```